Breakfast Cafe - The Sunny Nook

It is for my breakfast and lunch cafe with a hawaiian / beach theme. I am open 7 days a week from 7am to 2pm. We serve traditional American food such as omelettes, pancakes, burgers and sandwiches. I'll upload my old card and my new logo to be used. We have a lot of day to day regulars who eat there during the week, our t-shirts actually say 'Locals Only' on them. Hope this helps. Thanks.

Target Market(s)

anyone who has an appetite!

Industry/Entity Type

American Restaurant

Contact Information for Business Card

4815C Marlow Grove Avenue
Long Beach, California
(555) 731-2294

Requirements
Must have
• Address and phone number easily readable.
Nice to have
• beach or tropical theme

```html
<!DOCTYPE html>
<html lang="en">
<head>
<meta charset="utf-8">
<title>The Sunny Nook – Business Card</title>
<link rel="stylesheet" href="https://fonts.googleapis.com/css2?family=Bebas+Neue&display=swap">
<style>
  :root {
    --backdrop: #e6e1d8;
    --card-cream: #efe5d0;
    --card-cream-deep: #e6d9bd;
    --card-black: #1b1c1e;
    --stripe-yellow: #f6c02a;
    --stripe-orange: #c9781c;
    --ink: #161616;
    --accent-orange: #f2a33c;
    --accent-blue: #4db5d3;
    --tagline-brown: #a9661f;
    --badge-fill: #f0a23a;
  }
  * { margin: 0; padding: 0; box-sizing: border-box; }
  html, body {
    width: 1200px;
    height: 960px;
    overflow: hidden;
    background: var(--backdrop);
    font-family: "Bebas Neue", "Arial Narrow", sans-serif;
  }
  .business-card {
    position: absolute;
    left: 300px;
    top: 310px;
    width: 600px;
    height: 342px;
    border-radius: 18px;
    overflow: hidden;
    background: radial-gradient(ellipse at 60% 30%, var(--card-cream), var(--card-cream-deep));
    box-shadow: 0 4px 10px rgba(0, 0, 0, 0.35);
  }
  .card-wave {
    position: absolute;
    inset: 0;
    width: 600px;
    height: 342px;
  }
  .brand-badge {
    position: absolute;
    left: 86px;
    top: 30px;
    width: 160px;
    height: 160px;
    border-radius: 50%;
    background: radial-gradient(circle at 50% 40%, #f7c063, var(--badge-fill) 70%, #b8762a);
  }
  .brand-name {
    position: absolute;
    left: 36px;
    top: 200px;
    width: 260px;
    text-align: center;
    font-size: 42px;
    line-height: 1;
    color: var(--accent-blue);
    letter-spacing: 1px;
  }
  .brand-tagline {
    position: absolute;
    left: 36px;
    top: 252px;
    width: 260px;
    text-align: center;
    font-size: 13px;
    line-height: 1;
    letter-spacing: 4px;
    color: var(--tagline-brown);
  }
  .contact-block {
    position: absolute;
    right: 40px;
    top: 68px;
    text-align: right;
    color: var(--ink);
  }
  .contact-phone {
    font-size: 30px;
    line-height: 1;
    letter-spacing: 0.5px;
  }
  .contact-address {
    font-size: 22px;
    line-height: 23px;
    margin-top: 2px;
  }
  .service-line {
    position: absolute;
    left: 33px;
    top: 295px;
    font-size: 25px;
    line-height: 1;
    letter-spacing: 0.3px;
    white-space: nowrap;
  }
  .service-type { color: var(--accent-orange); margin-right: 6px; }
  .service-hours { color: var(--accent-blue); }
</style>
</head>
<body>
  <div class="business-card">
    <svg class="card-wave" viewBox="0 0 600 342" aria-hidden="true">
      <path fill="var(--stripe-yellow)" d="M0,170 C120,128 250,148 360,206 C450,252 540,225 600,172 L600,342 L0,342 Z"/>
      <path fill="var(--stripe-orange)" d="M0,170 C120,128 250,148 360,210 C450,260 540,236 600,188 L600,342 L0,342 Z"/>
      <path fill="var(--card-black)" d="M0,170 C120,128 250,148 360,214 C450,266 540,248 600,202 L600,342 L0,342 Z"/>
    </svg>

    <div class="brand-badge" role="img" aria-label="Cafe emblem badge"></div>
    <div class="brand-name">The Sunny Nook</div>
    <div class="brand-tagline">Long Beach, CA</div>

    <div class="contact-block">
      <div class="contact-phone">P.(555) 731-2294</div>
      <div class="contact-address">4815C Marlow Grove Avenue<br>Long Beach, California</div>
    </div>

    <div class="service-line">
      <span class="service-type">Breakfast &amp; Lunch Cafe</span>
      <span class="service-hours">Open 7 days a week from 7am to 2pm.</span>
    </div>
  </div>
</body>
</html>
```